Brightgate Audio Video Security LLC

Need help designing a web page for an alarm company. I want to promote my business.

Target Market(s)

Residential and commercial clients

Industry/Entity Type

Security Service

Coding

Coded - Design and coding required

Number of Pages Required

2 page

Font styles to use
Sans Serif

Requirements
Must have
• I would llike my logo displayed on the page. I would like my slogan displayed as well
´´A GREAT PLACE FOR YOUR SECURITY NEEDS´´
We are licensed and insured
Company phone number 555-555-0147
Company hours: Monday-Friday 8am-5pm Company address: P.O. Box 419 Ashby Falls, TX 79519 over 25 years experience
Email info. Brightgatesys@kelvamail.com
Company license #K41862509
Fire license# MTQ-6071852
LUV-8146027
We offer alarm monitoring,security cameras, access control,gate openers, home theater systems, covert camera installations, FIre alarm installation and monitoring
Nice to have
• We offer security at competitive prices.
Get customer information for a free quote similar to qmr website.
Should not have
• No prices listed on website

```html
<!DOCTYPE html>
<html lang="en">
<head>
<meta charset="utf-8">
<title>Brightgate Audio Video Security LLC</title>
<link href="https://fonts.googleapis.com/css2?family=Montserrat:wght@400;500;600;700;800&display=swap" rel="stylesheet">
<style>
:root{
  --red:#c8101f;
  --ink:#1b1b1b;
  --text:#3a3a3a;
  --light:#f4f0f0;
  --footer:#222222;
  --white:#ffffff;
  --line:#cfcfcf;
}
*{box-sizing:border-box;margin:0;padding:0}
html,body{width:1200px;height:3530px;overflow:hidden}
body{font-family:"Montserrat",sans-serif;color:var(--text);background:var(--white);position:relative}

/* header */
.site-header{position:absolute;left:0;top:0;width:1200px;height:126px;background:var(--white)}
.brand{position:absolute;left:133px;top:26px;width:180px;text-align:center}
.brand-name{font-weight:800;font-size:30px;letter-spacing:1px;color:var(--red);line-height:1}
.brand-tag{font-size:8px;font-weight:600;letter-spacing:1.5px;color:var(--ink);margin-top:6px;border-top:1px solid var(--ink);padding-top:3px;white-space:nowrap}
.brand-dot{width:22px;height:22px;border-radius:50%;background:var(--red);margin:0 auto 6px}
.contact-item{position:absolute;top:28px;display:flex;align-items:center;gap:10px;white-space:nowrap}
.contact-item .lbl{font-size:11px;font-weight:600;color:var(--ink)}
.contact-item .val{font-size:13px;font-weight:500;color:var(--ink)}
.contact-item .val.phone{font-size:20px;font-weight:600;color:var(--red)}
.btn{display:inline-block;background:var(--red);color:var(--white);font-weight:700;text-transform:uppercase;text-align:center;white-space:nowrap}
.btn-quote{position:absolute;left:944px;top:28px;width:123px;height:35px;line-height:35px;font-size:12px}
.main-nav{position:absolute;left:463px;top:90px;display:flex;gap:29px;font-size:12px;font-weight:600;color:var(--ink);white-space:nowrap}
.main-nav .active{color:var(--red);border-bottom:1px solid var(--red);padding-bottom:2px}

/* hero */
.hero{position:absolute;left:0;top:126px;width:1200px;height:548px;background:linear-gradient(90deg,#b39a78 0%,#d5c6ae 30%,#6f6a66 48%,#4a4542 62%,#8a7060 80%,#a67e62 100%)}
.hero-panel{position:absolute;left:726px;top:86px;width:474px;height:213px;background:rgba(60,60,60,.78);padding:20px 0 0 55px}
.hero-title{font-size:39px;font-weight:800;color:var(--white);line-height:46px;text-transform:uppercase;white-space:nowrap}
.hero .btn{margin-top:16px;width:120px;height:35px;line-height:35px;font-size:12px}
.dots{position:absolute;left:555px;top:496px;display:flex;gap:12px}
.dots span{width:9px;height:9px;border-radius:50%;background:var(--white)}
.dots span.on{background:var(--red)}

/* section titles */
.section-title{position:absolute;left:0;width:1200px;text-align:center;font-size:26px;font-weight:800;color:var(--ink)}
.section-title::after{content:"";display:block;width:48px;height:3px;background:#a9a9a9;margin:14px auto 0}

/* services */
.tile{position:absolute;width:265px;height:246px;overflow:hidden}
.tile-bar{position:absolute;left:0;bottom:0;width:100%;height:40px;background:rgba(40,40,40,.72);color:var(--white);font-size:12px;font-weight:700;text-transform:uppercase;line-height:40px;padding-left:15px;white-space:nowrap}
.tile-bar svg{position:absolute;right:14px;top:13px}

/* welcome */
.welcome{position:absolute;left:0;top:1354px;width:1200px;height:430px;background:linear-gradient(135deg,#2a2a2a,#151515)}
.welcome-copy{position:absolute;left:134px;top:52px;width:390px;color:var(--white)}
.welcome-copy .small{font-size:21px;font-weight:500}
.welcome-copy h2{font-size:28px;font-weight:800;line-height:35px;margin-top:8px}
.welcome-copy p{font-size:13.5px;line-height:19.5px;color:#cfcfcf;margin-top:26px}
.welcome-copy .btn{margin-top:26px;width:104px;height:32px;line-height:32px;font-size:11px}
.welcome-mark{position:absolute;left:560px;top:90px;width:520px;height:250px;display:flex;align-items:center;justify-content:center;gap:18px}
.welcome-mark .circle{width:60px;height:60px;border-radius:50%;background:var(--red);flex:none}
.welcome-mark .word{font-size:56px;font-weight:800;color:var(--red);letter-spacing:2px}

/* advantages */
.advantages{position:absolute;left:0;top:1784px;width:1200px;height:446px;background:var(--light)}
.adv{position:absolute;top:142px;width:260px;text-align:center}
.adv-icon{width:86px;height:86px;border-radius:50%;background:var(--red);margin:0 auto;display:flex;align-items:center;justify-content:center}
.adv h3{font-size:15px;font-weight:700;color:var(--ink);line-height:19px;margin-top:28px;text-transform:uppercase}
.adv p{font-size:13px;line-height:17.5px;margin-top:22px;color:var(--text)}

/* features */
.features-art{position:absolute;left:212px;top:2370px;width:761px;height:384px;background:radial-gradient(ellipse at 40% 60%,#d9d9d9 0%,#eeeeee 45%,#ffffff 75%)}

/* quote */
.quote{position:absolute;left:0;top:2800px;width:1200px;height:335px;background:var(--light)}
.quote h2{position:absolute;left:130px;top:60px;font-size:25px;font-weight:800;color:var(--ink)}
.quote h2::after{content:"";display:block;width:48px;height:3px;background:#a9a9a9;margin-top:14px}
.quote-text{position:absolute;left:130px;top:128px;width:380px;font-size:15px;line-height:22px;color:var(--text)}
.quote-call{position:absolute;left:188px;top:236px}
.quote-call .lbl{font-size:16px;font-weight:600;color:var(--ink)}
.quote-call .val{font-size:27px;font-weight:600;color:var(--red);margin-top:2px}
.field{position:absolute;height:42px;background:var(--white);border:1px solid var(--line);font-size:11px;font-weight:600;color:var(--ink);line-height:40px;padding-left:16px}
.btn-submit{position:absolute;left:633px;top:230px;width:400px;height:57px;line-height:57px;font-size:17px}

/* footer */
.site-footer{position:absolute;left:0;top:3135px;width:1200px;height:395px;background:var(--footer);color:var(--white)}
.foot-brand{position:absolute;left:133px;top:52px;width:272px;text-align:center}
.foot-brand .brand-dot{width:44px;height:44px;margin-bottom:12px}
.foot-brand .brand-name{font-size:40px;color:var(--red)}
.foot-brand .brand-tag{color:var(--white);border-color:var(--white);font-size:11px}
.foot-col{position:absolute;top:60px}
.foot-col h4{font-size:12px;font-weight:700;letter-spacing:.5px}
.foot-menu{list-style:none;margin-top:23px;font-size:11px;line-height:19.5px}
.foot-row{display:flex;gap:12px;align-items:flex-start;font-size:11px;line-height:15px;margin-top:20px;white-space:nowrap}
.foot-row:first-of-type{margin-top:23px}
.ic{flex:none;width:22px;height:22px;border-radius:50%;background:var(--white);display:flex;align-items:center;justify-content:center}
.foot-rule{position:absolute;left:133px;top:271px;width:935px;height:1px;background:#444}
.foot-legal{position:absolute;top:294px;font-size:11px;color:#dcdcdc;white-space:nowrap}
.copyright{position:absolute;left:0;top:355px;width:1200px;text-align:center;font-size:9px;color:#cfcfcf}
</style>
</head>
<body>

<header class="site-header">
  <div class="brand">
    <div class="brand-dot"></div>
    <div class="brand-name">BRIGHTGATE</div>
    <div class="brand-tag">AUDIO VIDEO SECURITY</div>
  </div>
  <div class="contact-item" style="left:478px">
    <svg width="28" height="22" viewBox="0 0 28 22"><rect x="1.5" y="1.5" width="25" height="19" fill="none" stroke="#c8101f" stroke-width="2"/><path d="M2 2l12 10 12-10M2 20l9-9M26 20l-9-9" fill="none" stroke="#c8101f" stroke-width="2"/></svg>
    <div><div class="lbl">E MAIL US</div><div class="val">Brightgatesys@kelvamail.com</div></div>
  </div>
  <div class="contact-item" style="left:752px">
    <svg width="28" height="28" viewBox="0 0 24 24"><path fill="#c8101f" d="M6.6 10.8a15.1 15.1 0 006.6 6.6l2.2-2.2c.3-.3.7-.4 1-.2 1.1.4 2.3.6 3.6.6.6 0 1 .4 1 1V20c0 .6-.4 1-1 1A17 17 0 013 4c0-.6.4-1 1-1h3.5c.6 0 1 .4 1 1 0 1.3.2 2.5.6 3.6.1.3 0 .7-.2 1z"/></svg>
    <div><div class="lbl">CALL US</div><div class="val phone">555-555-0147</div></div>
  </div>
  <a class="btn btn-quote">GET A QUOTE</a>
  <nav class="main-nav">
    <span class="active">HOME</span><span>ABOUT US</span><span>PACKAGES</span><span>SERVICES</span><span>PRODUCTS</span><span>BLOG</span><span>CONTACT US</span>
  </nav>
</header>

<section class="hero" role="img" aria-label="Hand pressing a finger on a keypad and fingerprint access control reader mounted beside a glass door">
  <div class="hero-panel">
    <h1 class="hero-title">A great<br>place for your<br>security needs</h1>
    <a class="btn">READ MORE</a>
  </div>
  <div class="dots"><span></span><span></span><span class="on"></span><span></span><span></span></div>
</section>

<h2 class="section-title" style="top:720px">OUR SERVICES</h2>

<div class="tile" style="left:53px;top:806px;background:linear-gradient(160deg,#e6e6e6,#bdbdbd 60%,#c98b8b)" role="img" aria-label="Ceiling smoke detector with red light">
  <div class="tile-bar">Alarm Monitoring<svg width="8" height="14" viewBox="0 0 8 14"><path d="M1 1l6 6-6 6" stroke="#fff" stroke-width="2" fill="none"/></svg></div></div>
<div class="tile" style="left:331px;top:806px;background:linear-gradient(160deg,#d8d2c8,#8b8378 55%,#4a4540)" role="img" aria-label="Wall mounted security camera">
  <div class="tile-bar">Security Cameras<svg width="8" height="14" viewBox="0 0 8 14"><path d="M1 1l6 6-6 6" stroke="#fff" stroke-width="2" fill="none"/></svg></div></div>
<div class="tile" style="left:607px;top:806px;background:linear-gradient(90deg,#b39a78,#5a5552 45%,#8a7060)" role="img" aria-label="Fingerprint access control keypad">
  <div class="tile-bar">Access Control<svg width="8" height="14" viewBox="0 0 8 14"><path d="M1 1l6 6-6 6" stroke="#fff" stroke-width="2" fill="none"/></svg></div></div>
<div class="tile" style="left:883px;top:806px;background:linear-gradient(160deg,#b06a4e,#8a5a48 45%,#cfcfcf)" role="img" aria-label="Driver's hand reaching from a car window toward a gate opener">
  <div class="tile-bar">Gate Openers<svg width="8" height="14" viewBox="0 0 8 14"><path d="M1 1l6 6-6 6" stroke="#fff" stroke-width="2" fill="none"/></svg></div></div>

<div class="tile" style="left:53px;top:1062px;background:linear-gradient(180deg,#e4d8c8,#c9b8a0 60%,#5a3a28)" role="img" aria-label="Home theater with television and speakers">
  <div class="tile-bar">Home Theater Systems<svg width="8" height="14" viewBox="0 0 8 14"><path d="M1 1l6 6-6 6" stroke="#fff" stroke-width="2" fill="none"/></svg></div></div>
<div class="tile" style="left:331px;top:1062px;background:linear-gradient(160deg,#9aa6ad,#e8e8e8 50%,#c9a890)" role="img" aria-label="Hands installing a small dome camera">
  <div class="tile-bar">Covert Camera Installations<svg width="8" height="14" viewBox="0 0 8 14"><path d="M1 1l6 6-6 6" stroke="#fff" stroke-width="2" fill="none"/></svg></div></div>
<div class="tile" style="left:607px;top:1062px;background:linear-gradient(160deg,#b5242a,#e9e6e3 45%,#f2f2f2)" role="img" aria-label="Technician fitting a fire alarm detector">
  <div class="tile-bar">Fire Alarm Installation<svg width="8" height="14" viewBox="0 0 8 14"><path d="M1 1l6 6-6 6" stroke="#fff" stroke-width="2" fill="none"/></svg></div></div>
<div class="tile" style="left:883px;top:1062px;background:linear-gradient(160deg,#c8ccd0,#3b4a5c 50%,#1a2a40)" role="img" aria-label="Operator watching monitoring screens">
  <div class="tile-bar">Monitoring<svg width="8" height="14" viewBox="0 0 8 14"><path d="M1 1l6 6-6 6" stroke="#fff" stroke-width="2" fill="none"/></svg></div></div>

<section class="welcome">
  <div class="welcome-copy">
    <div class="small">Welcome to</div>
    <h2>Brightgate Audio Video Security LLC</h2>
    <p>Lorem ipsum dolor sit amet, consectetur adipiscing elit, sed do eiusmod tempor incididunt ut labore et dolore magna aliqua. Ut enim ad minim veniam, quis nostrud exercitation ullamco laboris nisi ut aliquip ex ea commodo consequat. Duis aute irure dolor in reprehenderit in voluptate velit esse cillum dolore eu fugiat nulla pariatur. Excepteur sint occaecat cupidatat non proident.</p>
    <a class="btn">READ MORE</a>
  </div>
  <div class="welcome-mark">
    <div class="circle"></div>
    <div class="word">BRIGHTGATE</div>
  </div>
</section>

<section class="advantages">
  <h2 class="section-title" style="top:58px">ADVANTAGES</h2>
  <div class="adv" style="left:114px">
    <div class="adv-icon"><svg width="44" height="40" viewBox="0 0 44 40"><path d="M4 20L22 5l18 15" fill="none" stroke="#fff" stroke-width="3.5"/><rect x="10" y="19" width="24" height="18" fill="none" stroke="#fff" stroke-width="3"/><rect x="19" y="26" width="6" height="11" fill="#fff"/></svg></div>
    <h3>Smart Home<br>Security</h3>
    <p>Lorem ipsum dolor sit amet, consectetur adipiscing elit, sed do eiusmod tempor incididunt ut labore et dolore magna aliqua Ut enim ad minim veniam.</p>
  </div>
  <div class="adv" style="left:470px">
    <div class="adv-icon"><svg width="46" height="40" viewBox="0 0 46 40"><rect x="3" y="3" width="40" height="26" rx="2" fill="none" stroke="#fff" stroke-width="3"/><path d="M8 22l8-8 6 5 8-9 8 7" fill="none" stroke="#fff" stroke-width="2.5"/><path d="M17 36h12M23 29v7" stroke="#fff" stroke-width="3"/></svg></div>
    <h3>24/7 Professional<br>Monitoring</h3>
    <p>Lorem ipsum dolor sit amet, consectetur adipiscing elit, sed do eiusmod tempor incididunt ut labore et dolore magna aliqua Ut enim ad minim veniam.</p>
  </div>
  <div class="adv" style="left:825px">
    <div class="adv-icon"><svg width="38" height="44" viewBox="0 0 38 44"><path d="M19 2l16 6v12c0 11-7 18-16 22C10 38 3 31 3 20V8z" fill="#fff"/><path d="M11 22l6 6 11-12" fill="none" stroke="#c8101f" stroke-width="4"/></svg></div>
    <h3>6-Month<br>Guarantee</h3>
    <p>Lorem ipsum dolor sit amet, consectetur adipiscing elit, sed do eiusmod tempor incididunt ut labore et dolore magna aliqua Ut enim ad minim veniam.</p>
  </div>
</section>

<h2 class="section-title" style="top:2276px">FEATURES</h2>
<div class="features-art" role="img" aria-label="Illustrated house surrounded by smart home feature labels such as lights, thermostats, security panel, solar panels, live video, garage door, door locks, shades, security sensors, wellness and image capture, beside a smartphone showing a home control app"></div>

<section class="quote">
  <h2>GET A FREE QUOTE</h2>
  <p class="quote-text">At vero eos et accusamus et iusto odio dignissi mos ducimus qui blanditiis praesentium volup tatum deleniti atque corrupti quos dolores et quas molestias excepturi.</p>
  <div class="quote-call"><div class="lbl">CALL US</div><div class="val">555-555-0147</div></div>
  <div class="field" style="left:633px;top:60px;width:400px">NAME</div>
  <div class="field" style="left:633px;top:115px;width:400px">E MAIL</div>
  <div class="field" style="left:633px;top:170px;width:195px">PHONE</div>
  <div class="field" style="left:838px;top:170px;width:195px">ZIP</div>
  <a class="btn btn-submit">GET A FREE QUOTE</a>
</section>

<footer class="site-footer">
  <div class="foot-brand">
    <div class="brand-dot"></div>
    <div class="brand-name">BRIGHTGATE</div>
    <div class="brand-tag">AUDIO VIDEO SECURITY</div>
  </div>
  <div class="foot-col" style="left:506px">
    <h4>MENU</h4>
    <ul class="foot-menu"><li>HOME</li><li>ABOUT US</li><li>PACKAGES</li><li>SERVICES</li><li>PRODUCTS</li><li>BLOG</li><li>CONTACT US</li></ul>
  </div>
  <div class="foot-col" style="left:697px">
    <h4>CONTACT US</h4>
    <div class="foot-row"><span class="ic"><svg width="10" height="13" viewBox="0 0 10 13"><path d="M5 0a5 5 0 00-5 5c0 4 5 8 5 8s5-4 5-8a5 5 0 00-5-5zm0 7a2 2 0 110-4 2 2 0 010 4z" fill="#222"/></svg></span><span>P.O. Box 419 Ashby Falls,<br>TX 79519</span></div>
    <div class="foot-row"><span class="ic"><svg width="11" height="11" viewBox="0 0 24 24"><path fill="#222" d="M6.6 10.8a15.1 15.1 0 006.6 6.6l2.2-2.2c.3-.3.7-.4 1-.2 1.1.4 2.3.6 3.6.6.6 0 1 .4 1 1V20c0 .6-.4 1-1 1A17 17 0 013 4c0-.6.4-1 1-1h3.5c.6 0 1 .4 1 1 0 1.3.2 2.5.6 3.6.1.3 0 .7-.2 1z"/></svg></span><span>Call Us<br>555-555-0147</span></div>
    <div class="foot-row"><span class="ic"><svg width="11" height="8" viewBox="0 0 11 8"><rect width="11" height="8" fill="#222"/><path d="M0 0l5.5 4.5L11 0" stroke="#fff" fill="none"/></svg></span><span>E mail Us<br>Brightgatesys@kelvamail.com</span></div>
  </div>
  <div class="foot-col" style="left:967px">
    <h4>FOLLOW US</h4>
    <div class="foot-row"><span class="ic"></span><span>Like us on<br>CIRCLEBOOK</span></div>
    <div class="foot-row"><span class="ic"></span><span>Follow us on<br>CHIRPER</span></div>
    <div class="foot-row"><span class="ic"></span><span>Follow us on<br>WORKLINK</span></div>
  </div>
  <div class="foot-rule"></div>
  <div class="foot-legal" style="left:127px">COMPANY HOURS: MONDAY-FRIDAY 8AM-5PM</div>
  <div class="foot-legal" style="left:549px">COMPANY LICENSE #K41862509 &nbsp;&nbsp;&nbsp;| &nbsp;&nbsp;&nbsp;FIRE LICENSE# MTQ-6071852 &nbsp;&nbsp;&nbsp;| &nbsp;&nbsp;&nbsp;LUV-8146027</div>
  <div class="copyright">Copyright © 2020 All Rights Reserved</div>
</footer>

</body>
</html>
```